Pretty up existing catalogue

Catalog available - should simply be made new / fresh - ideally in corel draw? Please use page 14 as a sample design! Many thanks. Otherwise you can let off steam completely in terms of design. Thanks

Target Market(s)

customers worldwide

Industry/Entity Type

Bau

Font styles to use
Serif
Sans Serif

Requirements
Must have
• Logo must remain the same, modern look
Nice to have
• fresh modern look
Should not have
• extreme colors, log change

```html
<!DOCTYPE html>
<html lang="de">
<head>
<meta charset="utf-8">
<title>Haltenadeln</title>
<link rel="stylesheet" href="https://fonts.googleapis.com/css2?family=Quicksand:wght@400;500;600;700&display=swap">
<style>
  :root {
    --stage: #e9e9e9;
    --ink: #2a2a2a;
    --body-ink: #3c3c3c;
    --header: #dccd00;
    --card: #e6e5e1;
    --blue: #3a3fc4;
    --red: #d93a36;
    --green: #1f7a1c;
    --black: #111111;
    --navy: #35329a;
    --orange: #d9502b;
    --lime: #12a43a;
    --signal: #d10d12;
  }
  * { box-sizing: border-box; margin: 0; padding: 0; }
  html, body { width: 1200px; height: 1024px; overflow: hidden; }
  body {
    background: var(--stage);
    font-family: "Quicksand", sans-serif;
    color: var(--ink);
    position: relative;
  }
  .sheet {
    position: absolute;
    left: 246px; top: 12px;
    width: 707px; height: 1000px;
    background: linear-gradient(160deg, #e4e7ec 0%, #dde1e6 55%, #e3ddd6 100%);
    overflow: hidden;
  }
  .masthead {
    position: absolute; left: 0; top: 0;
    width: 100%; height: 172px;
    background: var(--header);
  }
  .masthead h1 {
    position: absolute; left: 50px; top: 30px;
    font-size: 46px; font-weight: 700; letter-spacing: -0.5px;
    color: var(--ink);
  }
  .masthead p {
    position: absolute; left: 51px; top: 84px;
    font-size: 23px; font-weight: 400; line-height: 27px;
    color: #3a3a2a;
  }
  .fitting-photo {
    position: absolute; left: 480px; top: 17px;
    width: 200px; height: 146px;
    border-radius: 40px 60px 70px 40px;
    background: radial-gradient(ellipse at 45% 40%, #ffffff 0%, #eeeeee 55%, #c9c9c9 100%);
  }
  .card {
    position: absolute;
    width: 292px; height: 177px;
    background: var(--card);
    border-radius: 9px;
    box-shadow: 0 2px 6px rgba(0,0,0,.12);
  }
  .band {
    height: 36px;
    border-radius: 9px 9px 0 0;
    color: #fff;
    font-size: 20px; font-weight: 400;
    padding: 5px 0 0 20px;
    white-space: nowrap;
  }
  .band b { font-weight: 600; }
  .spec {
    position: relative; z-index: 1;
    padding: 18px 0 0 20px;
    font-size: 13.5px; line-height: 16.5px;
    font-weight: 400; color: var(--body-ink);
    white-space: nowrap;
  }
  .spec strong { font-weight: 600; color: #222; display: block; margin-top: 3px; }
  .spec strong:first-child { margin-top: 0; }
  .spec .wide { display: block; }
  .pin-art {
    position: absolute; left: 186px; top: 12px;
    width: 90px; height: 84px;
    border-radius: 14px 14px 6px 6px;
  }
  .tool-art {
    position: absolute; left: 188px; top: 12px;
    width: 92px; height: 155px;
    border-radius: 8px;
    background: linear-gradient(135deg, rgba(40,40,40,.25), rgba(120,120,120,.15) 50%, rgba(200,60,60,.2));
  }
  .col-l { left: 52px; } .col-r { left: 361px; }
  .row-1 { top: 209px; } .row-2 { top: 402px; } .row-3 { top: 595px; } .row-4 { top: 788px; }
</style>
</head>
<body>
<main class="sheet">
  <header class="masthead">
    <h1>Haltenadeln</h1>
    <p>Zur Befestigung von Walder Schienen,<br>Folien und Rohrbögen auf Isolation</p>
    <div class="fitting-photo" role="img" aria-label="Weißes T-Rohrformstück"></div>
  </header>

  <section class="card col-l row-1">
    <div class="band" style="background:var(--blue)">Artikel Nr. <b>1140</b></div>
    <div class="pin-art" role="img" aria-label="Blaue Haltenadel" style="background:linear-gradient(180deg,rgba(58,63,196,.55),rgba(58,63,196,.15))"></div>
    <div class="spec"><strong>Länge:</strong><span class="wide">39 mm Für Rohre mit<br>einem 0 bis 20 mm</span><strong>Per Hand zu setzen Verpackung:</strong>500 Stück/Beutel und 5.000<br>Stück/Karton</div>
  </section>

  <section class="card col-r row-1">
    <div class="band" style="background:var(--red)">Artikel Nr. <b>1150</b></div>
    <div class="pin-art" role="img" aria-label="Rote Haltenadel" style="background:linear-gradient(180deg,rgba(217,58,54,.55),rgba(217,58,54,.15))"></div>
    <div class="spec"><strong>Länge:</strong><span class="wide">46 mm Für Rohre mit<br>einem Ø bis 20 mm</span><strong>Per Hand zu setzen Verpackung:</strong>500 Stück/Beutel und 5.000<br>Stück/Karton</div>
  </section>

  <section class="card col-l row-2">
    <div class="band" style="background:var(--green)">Artikel Nr. <b>1160</b></div>
    <div class="pin-art" role="img" aria-label="Grüne Haltenadel" style="background:linear-gradient(180deg,rgba(31,122,28,.55),rgba(31,122,28,.15))"></div>
    <div class="spec"><strong>Länge:</strong><span class="wide">61 mm Für Rohre mit<br>einem 0 bis 20 mm</span><strong>Per Hand zu setzen Verpackung:</strong>500 Stück/Beutel und 5.000<br>Stück/Karton</div>
  </section>

  <section class="card col-r row-2">
    <div class="band" style="background:var(--black)">Artikel Nr. <b>1255</b></div>
    <div class="pin-art" role="img" aria-label="Schwarze Haltenadel" style="background:linear-gradient(180deg,rgba(40,40,48,.55),rgba(40,40,48,.15))"></div>
    <div class="spec"><strong>Länge:</strong><span class="wide">52 mm Für Rohre mit<br>einem 0 bis 26 mm</span><strong>Per Hand zu setzen Verpackung:</strong>100 Stück/Beutel und 1.000<br>Stück/Karton</div>
  </section>

  <section class="card col-l row-3">
    <div class="band" style="background:var(--navy)">Artikel Nr. <b>FPN40</b></div>
    <div class="pin-art" role="img" aria-label="Dunkelblaue Haltenadel für Setzgerät" style="background:linear-gradient(180deg,rgba(53,50,154,.55),rgba(53,50,154,.15))"></div>
    <div class="spec"><strong>Länge:</strong><span class="wide">39 mm Für Rohre mit<br>einem Ø bis 20 mm</span><strong>Mit FixPin zu setzen Verpackung:</strong>250 Stück/Karton und Magaziniert<br>á 25 Stück</div>
  </section>

  <section class="card col-r row-3">
    <div class="band" style="background:var(--orange)">Artikel Nr. <b>FPN50</b></div>
    <div class="pin-art" role="img" aria-label="Orange Haltenadel für Setzgerät" style="background:linear-gradient(180deg,rgba(217,80,43,.55),rgba(217,80,43,.15))"></div>
    <div class="spec"><strong>Länge:</strong><span class="wide">47 mm Für Rohre mit<br>einem Ø bis 20 mm</span><strong>Mit FixPin zu setzen Verpackung:</strong>250 Stück/Karton und Magaziniert<br>á 25 Stück</div>
  </section>

  <section class="card col-l row-4">
    <div class="band" style="background:var(--lime)">Artikel Nr. <b>FPN60</b></div>
    <div class="pin-art" role="img" aria-label="Hellgrüne Haltenadel für Setzgerät" style="background:linear-gradient(180deg,rgba(18,164,58,.55),rgba(18,164,58,.15))"></div>
    <div class="spec"><strong>Länge:</strong><span class="wide">62 mm Für Rohre mit<br>einem 0 bis 20 mm</span><strong>Mit FixPin zu setzen Verpackung:</strong>250 Stück/Karton und Magaziniert<br>á 25 Stück</div>
  </section>

  <section class="card col-r row-4">
    <div class="band" style="background:var(--signal)">Artikel Nr. <b>FSG</b></div>
    <div class="tool-art" role="img" aria-label="Setzgerät mit Magazin für Haltenadeln"></div>
    <div class="spec"><strong>Setzgerät:</strong><span class="wide">für Haltenadeln FPN40,<br>FPN50 und FPN60</span><strong>Verpackung:</strong>1 Stück/Karton</div>
  </section>
</main>
</body>
</html>
```